New Business Card Design Project

I need a design for business cards, i am an electrical business called "Corvane Electrical and Communications" i need the cards to be double sided with the company logo on the back (attached) the front needs to say my company name, web site, email address, telephone number, and ABN number and electrical license number. I am open to different arrangements of the information but would like the background to be incorporating something electrical or something that looks smart. open to all additional ideas also.

The company colours are orange and grey see logo attached.

Business Name: Corvane Electrical and Communications
Website: corvaneelectricalandcomms.example.com.au
Email: brent@corvaneelectricalandcomms.example.com.au
Telephone(mobile): 0481209736
ABN: 71208349162
Lic No: 418273D

Target Market(s)

Business entities, Project Managers, Accounts, Clients

Industry/Entity Type

Electrician

Contact Information for Business Card

I need a design for business cards, i am an electrical business called "Corvane Electrical and Communications" i need the cards to be double sided with the company logo on the back (attached) the front needs to say my company name

Font styles to use
Serif
Sans Serif

Colors
f37122
5c5c5c

Requirements
Must have
• Must have the Logo on the back open to different ways of it being on the back but had in mind to keep it central but again open to other options
Nice to have
• A real modern cool background that is eye catching yet contemporary
Should not have
• No backgrounds of a light bulb or plug or anything like that

```html
<!DOCTYPE html>
<html lang="en">
<head>
<meta charset="utf-8">
<title>Corvane Electrical and Communications – Business Cards</title>
<link rel="stylesheet" href="https://fonts.googleapis.com/css2?family=Open+Sans:wght@400;600;700&display=swap">
<style>
  :root {
    --orange: #f5a21c;
    --grey: #5c5c5c;
    --grey-dark: #4f4f50;
    --white: #ffffff;
    --ink: #333333;
    --stage: #e9e9e9;
  }
  * { box-sizing: border-box; margin: 0; padding: 0; }
  html, body { width: 1200px; height: 900px; overflow: hidden; }
  body {
    background: var(--stage);
    font-family: "Open Sans", Arial, sans-serif;
    position: relative;
  }
  .card {
    position: absolute;
    width: 640px;
    height: 366px;
    border-radius: 22px;
    overflow: hidden;
    box-shadow: 0 10px 24px rgba(0,0,0,.18);
  }
  .card-back { left: 110px; top: 56px; background: var(--grey); }
  .card-front { left: 450px; top: 478px; background: var(--white); }

  .brand {
    color: var(--white);
    font-weight: 600;
    text-align: center;
    line-height: 1;
  }
  .brand-name { display: block; font-size: 64px; letter-spacing: 4px; text-transform: uppercase; }
  .brand-line { display: block; font-size: 15px; letter-spacing: 1.6px; margin-top: 8px; text-transform: uppercase; }

  .card-back .brand { position: absolute; left: 0; right: 0; top: 112px; }
  .card-back .website {
    position: absolute; right: 28px; bottom: 30px;
    color: var(--white); font-size: 13px;
  }

  .card-front .brand { position: absolute; right: 30px; top: 42px; color: var(--grey); text-align: right; }
  .card-front .brand-name { font-size: 46px; letter-spacing: 3px; }
  .card-front .brand-line { font-size: 11px; letter-spacing: 1px; margin-top: 6px; }
  .licence {
    position: absolute; right: 30px; top: 126px;
    color: var(--orange); font-size: 13px; font-weight: 600;
  }
  .licence span { color: var(--ink); font-weight: 400; }

  .edge-tab {
    position: absolute; left: 0; top: 34px; width: 8px; height: 26px;
    background: var(--grey); border-radius: 0 3px 3px 0;
  }
  .person { position: absolute; left: 30px; top: 30px; }
  .person-name { color: var(--orange); font-size: 24px; font-weight: 400; text-transform: uppercase; line-height: 1.1; }
  .person-role { color: var(--ink); font-size: 12px; font-weight: 600; text-transform: uppercase; letter-spacing: .5px; }

  .wave { position: absolute; inset: 0; }

  .contacts {
    position: absolute; left: 28px; top: 252px;
    list-style: none; color: var(--white); font-size: 13px; line-height: 24px;
  }
  .contacts li { display: flex; align-items: center; gap: 8px; }
  .contacts .label { color: var(--orange); font-weight: 700; }
  .contacts svg { width: 13px; height: 13px; flex: none; }
</style>
</head>
<body>

  <section class="card card-back" aria-label="Card back">
    <div class="brand">
      <span class="brand-name">Corvane</span>
      <span class="brand-line">Electrical &amp; Communications</span>
    </div>
    <p class="website">www.corvaneelectricalandcomms.example.com.au</p>
  </section>

  <section class="card card-front" aria-label="Card front">
    <svg class="wave" viewBox="0 0 640 366" aria-hidden="true">
      <path d="M0,232 C130,214 300,214 420,204 C520,196 600,176 640,160 L640,366 L0,366 Z" fill="#5c5c5c"/>
      <path d="M0,226 C130,208 300,208 420,198 C520,190 600,170 640,154" fill="none" stroke="#f5a21c" stroke-width="3"/>
    </svg>

    <span class="edge-tab"></span>
    <div class="person">
      <p class="person-name">Marlo Fennick</p>
      <p class="person-role">Director</p>
    </div>

    <div class="brand">
      <span class="brand-name">Corvane</span>
      <span class="brand-line">Electrical &amp; Communications</span>
    </div>
    <p class="licence">Lic No: <span>418273D</span></p>

    <ul class="contacts">
      <li><span class="label">ABN:</span> 71208349162</li>
      <li>
        <svg viewBox="0 0 16 16"><path d="M4 1l3 3-2 2c1 2 3 4 5 5l2-2 3 3-2 3C7 15 1 9 1 3z" fill="#f5a21c"/></svg>
        0481-209-736
      </li>
      <li>
        <svg viewBox="0 0 16 16"><rect x="1" y="3" width="14" height="10" fill="none" stroke="#f5a21c" stroke-width="1.6"/><path d="M1 3l7 6 7-6" fill="none" stroke="#f5a21c" stroke-width="1.6"/></svg>
        brent@corvaneelectricalandcomms.example.com.au
      </li>
      <li>
        <svg viewBox="0 0 16 16"><circle cx="8" cy="8" r="6.5" fill="none" stroke="#f5a21c" stroke-width="1.5"/><ellipse cx="8" cy="8" rx="3" ry="6.5" fill="none" stroke="#f5a21c" stroke-width="1.2"/><path d="M1.5 8h13" stroke="#f5a21c" stroke-width="1.2"/></svg>
        www.corvaneelectricalandcomms.example.com.au
      </li>
    </ul>
  </section>

</body>
</html>
```